Tidal Forge - Crypto Currency Miner Powered by Renewable Energy Website

We Need Web Pages Design for Website for Crypto Currency Miner

Serivices include:
Mining Rig Sales
Housing for Rigs turnkey on renewable energy grid
Cloud Mining term packages
Updates

http://www.vaultrigsurvey.example (Competitors sites)

Target Market(s)

Investers for Mining Rigs and terms for 1,2 or 3 years of Hash rate

Industry/Entity Type

Mining

Number of Pages Required

5+ page

Font styles to use
Sans Serif

Colors
add136
9bcb3c
606060
474747
ffc214
cadf82
fbee3e
876aae
6b449b

Requirements
Must have
• Pictures of Solar, Wind and power Factor Correction units
Nice to have
• e-commerce platform so contract terms can be purchased through website
Should not have
• Heavy construction equipment

```html
<!DOCTYPE html>
<html lang="en">
<head>
<meta charset="utf-8">
<title>Tidal Forge – Renewable Crypto Mining</title>
<link href="https://fonts.googleapis.com/css2?family=Montserrat:wght@400;600;700&family=Open+Sans:wght@400;600;700&display=swap" rel="stylesheet">
<style>
:root{
  --green:#8dc63f;
  --green-dark:#4fa333;
  --green-band:#8cc63f;
  --red:#e0141e;
  --ink:#222;
  --text:#606060;
  --footer:#1e1e1e;
  --light:#eef3f8;
  --grey-bg:#f2f2f2;
  --white:#fff;
}
*{margin:0;padding:0;box-sizing:border-box}
html,body{width:1200px;height:3468px;overflow:hidden}
body{position:relative;font-family:"Open Sans",sans-serif;color:var(--text);background:var(--white)}
.abs{position:absolute}
h1,h2,h3,.brand,.nav,.btn,.f-head{font-family:"Montserrat",sans-serif}

/* hero */
.hero{left:0;top:0;width:1200px;height:631px}
.hero-photo{position:absolute;inset:0;background:linear-gradient(180deg,#2d6fc9 0%,#6aa4e0 35%,#9cc2e4 52%,#6f8f3b 62%,#83a83a 80%,#6a8e2c 100%)}
.brand{display:flex;align-items:center;gap:12px;font-weight:700;font-size:36px;color:var(--white)}
.brand-dot{width:46px;height:46px;border-radius:50%;background:var(--green)}
.hero-brand{left:132px;top:66px}
.call{left:865px;top:21px;color:var(--white);font-size:13px;font-weight:600;display:flex;align-items:center;gap:8px}
.call b{font-family:"Montserrat",sans-serif;font-size:20px}
.nav{left:588px;top:58px;display:flex;gap:6px;font-size:12px;font-weight:700;color:var(--white)}
.nav span{padding:6px 10px}
.nav .active{background:var(--white);color:var(--green-dark)}
.hero-title{left:208px;top:425px;font-size:37px;line-height:46px;font-weight:700;color:var(--white);letter-spacing:1px}
.btn{display:flex;align-items:center;justify-content:center;font-weight:700;text-transform:uppercase}
.btn-red{left:210px;top:528px;width:153px;height:39px;background:var(--red);color:var(--white);font-size:16px}
.dots{left:548px;top:572px;display:flex;gap:12px}
.dots i{width:11px;height:11px;border-radius:50%;background:var(--white);display:block}
.dots i.on{background:transparent;border:2px solid var(--white)}

/* services */
.section-title{font-size:20px;font-weight:700;color:var(--ink);text-align:center;width:1200px;left:0}
.services-title{top:677px}
.services-sub{left:360px;top:722px;width:480px;text-align:center;font-size:14px;line-height:24px}
.service{width:240px;top:821px;text-align:center}
.service .ring{width:162px;height:162px;border-radius:50%;border:7px solid var(--green-dark);margin:0 auto;display:flex;align-items:center;justify-content:center}
.service h3{margin-top:46px;font-size:15px;line-height:20px;font-weight:700;color:var(--ink)}
.service p{margin-top:14px;font-size:12.5px;line-height:17px;padding:0 20px}

/* welcome */
.welcome-band{left:0;top:1207px;width:1200px;height:395px;background:var(--green-band)}
.welcome-mark{left:134px;top:1299px;width:208px;height:208px;border-radius:50%;border:10px solid var(--white);display:flex;align-items:center;justify-content:center;color:var(--white);font-family:"Montserrat",sans-serif;font-weight:700;font-size:26px}
.welcome-rule{left:417px;top:1260px;width:3px;height:277px;background:rgba(255,255,255,.6)}
.welcome-title{left:497px;top:1264px;font-size:25px;font-weight:700;color:var(--white)}
.welcome-lead{left:497px;top:1313px;width:500px;font-size:15px;line-height:21px;font-weight:700;color:var(--white)}
.welcome-body{left:497px;top:1383px;width:505px;font-size:12.5px;line-height:20px;color:var(--white)}
.btn-white{left:497px;top:1491px;width:127px;height:38px;background:var(--white);color:var(--green-dark);font-size:14px}

/* coins */
.coins{left:0;top:1602px;width:1200px;height:167px;background:var(--light)}
.coin{width:110px;top:1642px;text-align:center;font-size:13px;color:#444}
.coin i{display:block;width:50px;height:50px;border-radius:50%;margin:0 auto 14px}
.arrow{top:1652px;font-size:30px;color:#888}

/* profit */
.chart{left:100px;top:1840px}
.profit-title{left:682px;top:1858px;width:380px;font-size:32px;line-height:42px;font-weight:400;color:#333}
.profit-text{left:682px;top:1964px;width:360px;font-size:13px;line-height:21px}
.btn-green{background:var(--green);color:var(--white);font-size:14px}
.profit-btn{left:687px;top:2099px;width:127px;height:36px}

/* start mining */
.start-band{left:0;top:2266px;width:1200px;height:333px;background:linear-gradient(180deg,#3a3a3a,#262626)}
.start-title{left:0;top:2325px;width:1200px;text-align:center;font-size:36px;font-weight:700;color:var(--white)}
.start-text{left:360px;top:2382px;width:480px;text-align:center;font-size:14px;line-height:22px;color:#aaa}
.start-btn{left:522px;top:2487px;width:156px;height:44px;font-size:24px;color:#111}

/* testimonials */
.testimonials{left:0;top:2599px;width:1200px;height:494px;background:var(--grey-bg)}
.testimonials-title{top:2640px}
.title-rule{left:550px;top:2681px;width:100px;height:2px;background:#bbb}
.quote-card{left:289px;top:2728px;width:643px;height:190px;background:var(--white);box-shadow:0 2px 10px rgba(0,0,0,.08)}
.quote-card p{position:absolute;left:70px;top:40px;width:500px;text-align:center;font-size:12.5px;line-height:21px;color:#444}
.quote-mark{font-family:Georgia,serif;font-size:60px;color:#ccc;position:absolute;line-height:1}
.quote-open{left:48px;top:20px}
.quote-close{left:468px;top:118px}
.quote-tail{left:588px;top:2916px;width:0;height:0;border-left:14px solid transparent;border-right:14px solid transparent;border-top:14px solid var(--white)}
.avatar{left:571px;top:2959px;width:56px;height:56px;border-radius:50%;background:linear-gradient(180deg,#c9b8a8,#3c4a66)}
.person{left:0;top:3029px;width:1200px;text-align:center;font-size:13px;font-weight:700;color:#222}
.t-arrow{top:2980px;font-size:32px;color:#aaa}

/* footer */
.footer{left:0;top:3093px;width:1200px;height:375px;background:var(--footer)}
.footer-brand{left:132px;top:3200px;font-size:42px;color:var(--green)}
.footer-brand .brand-dot{width:60px;height:60px}
.f-head{font-size:13px;font-weight:700;color:var(--white)}
.f-col{top:3148px}
.f-col .f-head{margin-bottom:20px}
.f-list{font-size:12px;line-height:17px;color:#ddd}
.menu-list{line-height:15px}
.contact-item{display:flex;gap:14px;margin-bottom:14px;align-items:flex-start}
.newsletter-head{left:860px;top:3148px}
.email-box{left:860px;top:3193px;width:206px;height:39px;background:var(--white);font-size:12px;color:#777;padding:12px 0 0 12px}
.newsletter-btn{left:860px;top:3248px;width:72px;height:33px;font-size:12px;color:#111}
.f-rule{left:132px;top:3364px;width:936px;height:1px;background:#3a3a3a}
.follow{left:138px;top:3402px;display:flex;align-items:center;gap:12px}
.follow .f-head{font-size:12px;margin-right:10px}
.social{width:30px;height:30px;border-radius:50%;display:block}
.copyright{left:874px;top:3404px;font-size:12px;color:#ccc}
</style>
</head>
<body>

<!-- hero -->
<section class="hero abs">
  <div class="hero-photo" role="img" aria-label="Photo of solar panel arrays in a green field under a blue sky"></div>
  <div class="brand hero-brand abs"><span class="brand-dot"></span>Tidal Forge</div>
  <div class="call abs">
    <svg width="14" height="14" viewBox="0 0 24 24"><path fill="#fff" d="M6.6 10.8a15 15 0 0 0 6.6 6.6l2.2-2.2c.3-.3.7-.4 1-.2 1.1.4 2.3.6 3.6.6.6 0 1 .4 1 1V20c0 .6-.4 1-1 1A17 17 0 0 1 3 4c0-.6.4-1 1-1h3.5c.6 0 1 .4 1 1 0 1.3.2 2.5.6 3.6.1.3 0 .7-.2 1z"/></svg>
    CALL US : <b>555.014.2290</b>
  </div>
  <nav class="nav abs">
    <span class="active">HOME</span><span>ABOUT US</span><span>SERVICES</span><span>FEATURES</span><span>BLOG</span><span>CONTACT US</span>
  </nav>
  <h1 class="hero-title abs">GREEN ENERGY<br>TRADING PLATFORM</h1>
  <div class="btn btn-red abs">Read More</div>
  <div class="dots abs"><i></i><i></i><i class="on"></i><i></i><i></i></div>
</section>

<!-- services -->
<h2 class="section-title services-title abs">OUR SERVICES</h2>
<p class="services-sub abs">There are many variations of passages of Lorem Ipsum available but the majority have suffered alteration in some form.</p>

<div class="service abs" style="left:111px">
  <div class="ring"><svg width="80" height="80" viewBox="0 0 80 80"><circle cx="40" cy="40" r="32" fill="#8dc63f"/><circle cx="40" cy="40" r="24" fill="none" stroke="#fff" stroke-width="3"/><path d="M30 40h20M40 30v20" stroke="#fff" stroke-width="4"/></svg></div>
  <h3>MINE IN MULTIPLE<br>CRYPTOCURRENCIES</h3>
  <p>There are many variations of passages of Lorem Ipsum available, but the majority have suffered alteration lorem.</p>
</div>
<div class="service abs" style="left:349px">
  <div class="ring"><svg width="90" height="80" viewBox="0 0 90 80"><circle cx="66" cy="16" r="9" fill="#f6b21a"/><path d="M20 30h44l10 30H10z" fill="#4fa333"/><path d="M25 40h50M18 50h60M34 30l-4 30M48 30v30M62 30l4 30" stroke="#fff" stroke-width="2"/><path d="M40 60h10v12H40zM30 72h30" stroke="#4fa333" stroke-width="4"/></svg></div>
  <h3>NATIONWIDE<br>ENERGY</h3>
  <p>There are many variations of passages of Lorem Ipsum available, but the majority have suffered alteration lorem.</p>
</div>
<div class="service abs" style="left:601px">
  <div class="ring"><svg width="80" height="80" viewBox="0 0 80 80"><rect x="14" y="50" width="10" height="18" fill="#8dc63f"/><rect x="30" y="40" width="10" height="28" fill="#8dc63f"/><rect x="46" y="32" width="10" height="36" fill="#4fa333"/><rect x="62" y="22" width="10" height="46" fill="#4fa333"/><path d="M12 40l18-14 12 8 24-20" fill="none" stroke="#4fa333" stroke-width="4"/><path d="M58 12h10v10" fill="none" stroke="#4fa333" stroke-width="4"/></svg></div>
  <h3>PROFITS BEYOND<br>EXPECTANCIES</h3>
  <p>There are many variations of passages of Lorem Ipsum available, but the majority have suffered alteration lorem.</p>
</div>
<div class="service abs" style="left:858px">
  <div class="ring"><svg width="80" height="80" viewBox="0 0 80 80"><rect x="30" y="14" width="38" height="24" rx="3" fill="#8dc63f"/><rect x="30" y="20" width="38" height="5" fill="#4fa333"/><path d="M10 56c10-8 18-10 28-6h14c4 0 4 6 0 6H38m-28 8 8 4h26l20-14c3-3 0-7-4-5L52 56" fill="none" stroke="#4fa333" stroke-width="4" stroke-linejoin="round"/></svg></div>
  <h3>GET YOUR FIRST<br>PAYOUT TODAY</h3>
  <p>There are many variations of passages of Lorem Ipsum available, but the majority have suffered alteration lorem.</p>
</div>

<!-- welcome -->
<section class="welcome-band abs"></section>
<div class="welcome-mark abs">Tidal Forge</div>
<div class="welcome-rule abs"></div>
<h2 class="welcome-title abs">WELCOME TO OUR SITE</h2>
<p class="welcome-lead abs">There are many variations of passages of Lorem Ipsum available but the majority have suffered alteration in some form.</p>
<p class="welcome-body abs">It is a long established fact that a reader will be distracted by the readable content of a page when looking at its layout. The point of using Lorem Ipsum is that it has a more-or-less normal distribution of letters as opposed to using 'Content here, content here', making it look like readable English. Many desktop publishing packages and web.</p>
<div class="btn btn-white abs">Read More</div>

<!-- coins -->
<section class="coins abs"></section>
<div class="arrow abs" style="left:62px">&#8249;</div>
<div class="arrow abs" style="left:1124px">&#8250;</div>
<div class="coin abs" style="left:105px"><i style="background:#f7931a"></i>Solcoin</div>
<div class="coin abs" style="left:202px"><i style="background:#4c5a7a"></i>Aethon</div>
<div class="coin abs" style="left:313px"><i style="background:#1e5a8a"></i>Ripen</div>
<div class="coin abs" style="left:426px"><i style="background:#f7931a;border:6px solid #e7c583"></i>Solcoin Gold</div>
<div class="coin abs" style="left:542px"><i style="background:#222"></i>Kardo</div>
<div class="coin abs" style="left:666px"><i style="background:#d4d4d4;border:4px solid #b5b5b5"></i>Litewave</div>
<div class="coin abs" style="left:784px"><i style="background:#3cbeb0;border:4px solid #f5b326"></i>Nemora</div>
<div class="coin abs" style="left:884px"><i style="background:#58bf00"></i>Neon</div>
<div class="coin abs" style="left:988px"><i style="background:#3aa3e3"></i>Starlit</div>

<!-- profit chart -->
<svg class="chart abs" width="490" height="340" viewBox="0 0 490 340" role="img" aria-label="Mining profit line and area chart">
  <g stroke="#dfe6ea" stroke-width="1">
    <line x1="50" y1="300" x2="470" y2="300"/><line x1="50" y1="244" x2="470" y2="244"/><line x1="50" y1="188" x2="470" y2="188"/><line x1="50" y1="132" x2="470" y2="132"/><line x1="50" y1="76" x2="470" y2="76"/><line x1="50" y1="20" x2="470" y2="20"/>
  </g>
  <g font-family="Open Sans,sans-serif" font-size="12" fill="#333" text-anchor="end">
    <text x="40" y="304">0</text><text x="40" y="248">2</text><text x="40" y="192">4</text><text x="40" y="136">6</text><text x="40" y="80">8</text><text x="40" y="24">10</text>
  </g>
  <g font-family="Open Sans,sans-serif" font-size="12" fill="#333" text-anchor="middle">
    <text x="60" y="324">1</text><text x="104" y="324">2</text><text x="148" y="324">3</text><text x="192" y="324">4</text><text x="236" y="324">5</text><text x="280" y="324">6</text><text x="324" y="324">7</text><text x="368" y="324">8</text><text x="412" y="324">9</text><text x="456" y="324">10</text>
  </g>
  <path d="M60 118L104 132L148 76L192 118L236 76L280 188L324 20L368 118L412 244L456 104V300H60Z" fill="#2aa6a0" fill-opacity=".35"/>
  <path d="M60 160L104 272L148 174L192 230L236 188L280 230L324 90L368 62L412 132L456 76V300H60Z" fill="#8dc63f" fill-opacity=".45"/>
  <polyline points="60,118 104,132 148,76 192,118 236,76 280,188 324,20 368,118 412,244 456,104" fill="none" stroke="#1f8fb0" stroke-width="2"/>
  <polyline points="60,160 104,272 148,174 192,230 236,188 280,230 324,90 368,62 412,132 456,76" fill="none" stroke="#6cbf3c" stroke-width="2"/>
  <polyline points="60,244 104,174 148,202 192,216 236,132 280,104 324,146 368,104 412,216 456,132" fill="none" stroke="#2aa6a0" stroke-width="2"/>
  <g fill="#1f8fb0"><circle cx="60" cy="118" r="5"/><circle cx="104" cy="132" r="5"/><circle cx="148" cy="76" r="5"/><circle cx="192" cy="118" r="5"/><circle cx="236" cy="76" r="5"/><circle cx="280" cy="188" r="5"/><circle cx="324" cy="20" r="5"/><circle cx="368" cy="118" r="5"/><circle cx="412" cy="244" r="5"/><circle cx="456" cy="104" r="5"/></g>
  <g fill="#6cbf3c"><circle cx="60" cy="160" r="5"/><circle cx="104" cy="272" r="5"/><circle cx="148" cy="174" r="5"/><circle cx="192" cy="230" r="5"/><circle cx="236" cy="188" r="5"/><circle cx="280" cy="230" r="5"/><circle cx="324" cy="90" r="5"/><circle cx="368" cy="62" r="5"/><circle cx="412" cy="132" r="5"/><circle cx="456" cy="76" r="5"/></g>
  <g fill="#2aa6a0"><circle cx="60" cy="244" r="5"/><circle cx="104" cy="174" r="5"/><circle cx="148" cy="202" r="5"/><circle cx="192" cy="216" r="5"/><circle cx="236" cy="132" r="5"/><circle cx="280" cy="104" r="5"/><circle cx="324" cy="146" r="5"/><circle cx="368" cy="104" r="5"/><circle cx="412" cy="216" r="5"/><circle cx="456" cy="132" r="5"/></g>
  <g font-family="Open Sans,sans-serif" font-size="10" font-weight="700" text-anchor="middle">
    <text x="60" y="104" fill="#1f8fb0">1-7</text><text x="192" y="104" fill="#1f8fb0">4-7</text><text x="324" y="10" fill="#1f8fb0">7-10</text><text x="368" y="50" fill="#6cbf3c">8-8</text><text x="456" y="92" fill="#1f8fb0">10-10</text><text x="104" y="160" fill="#2aa6a0">2-4</text>
  </g>
</svg>
<h2 class="profit-title abs">Making the most profit<br>while mining</h2>
<p class="profit-text abs">There are many variations of passages of Lorem Ipsum available, but the majority have suffered alteration in some form, by injected humour, or randomised words which don't look even slightly believable. If you are going to use a passage of Lorem Ipsum, you need to be sure there.</p>
<div class="btn btn-green profit-btn abs">Read More</div>

<!-- start mining -->
<section class="start-band abs" role="img" aria-label="Darkened photo of a city skyline at night"></section>
<h2 class="start-title abs">START MINING NOW</h2>
<p class="start-text abs">There are many variations of passages of Lorem Ipsum available, but the majority have suffered alteration in some form, by injected humour, or randomised words which don't look even.</p>
<div class="btn btn-green start-btn abs">Signup</div>

<!-- testimonials -->
<section class="testimonials abs"></section>
<h2 class="section-title testimonials-title abs">CUSTOMER TESTIMONIALS</h2>
<div class="title-rule abs"></div>
<div class="quote-card abs">
  <span class="quote-mark quote-open">&ldquo;</span>
  <p>There are many variations of passages of Lorem Ipsum available, but the majority have suffered alteration in some form, by injected humour, or randomised words which don't look even slightly believable. If you are going to use a passage of Lorem Ipsum, you need to be sure there isn't anything embarrassing hidden in the middle of text. All the Lorem Ipsum generators on the Internet tend to repeat</p>
  <span class="quote-mark quote-close">&rdquo;</span>
</div>
<div class="quote-tail abs"></div>
<div class="t-arrow abs" style="left:480px">&#8249;</div>
<div class="avatar abs" role="img" aria-label="Customer portrait"></div>
<div class="t-arrow abs" style="left:708px">&#8250;</div>
<div class="person abs">Daniel Marsh</div>

<!-- footer -->
<footer class="footer abs"></footer>
<div class="brand footer-brand abs"><span class="brand-dot"></span>Tidal Forge</div>

<div class="f-col abs" style="left:481px">
  <div class="f-head">CONTACT US</div>
  <div class="f-list">
    <div class="contact-item"><svg width="10" height="14" viewBox="0 0 10 14"><path d="M5 0a5 5 0 0 1 5 5c0 4-5 9-5 9S0 9 0 5a5 5 0 0 1 5-5z" fill="#fff"/><circle cx="5" cy="5" r="2" fill="#1e1e1e"/></svg><span>87 Ridgeline Road<br>Harlow Falls, ST 00417</span></div>
    <div class="contact-item"><svg width="12" height="12" viewBox="0 0 24 24"><path fill="#fff" d="M6.6 10.8a15 15 0 0 0 6.6 6.6l2.2-2.2c.3-.3.7-.4 1-.2 1.1.4 2.3.6 3.6.6.6 0 1 .4 1 1V20c0 .6-.4 1-1 1A17 17 0 0 1 3 4c0-.6.4-1 1-1h3.5c.6 0 1 .4 1 1 0 1.3.2 2.5.6 3.6.1.3 0 .7-.2 1z"/></svg><span>555.014.2290</span></div>
    <div class="contact-item"><svg width="12" height="10" viewBox="0 0 12 10"><rect width="12" height="10" fill="#fff"/><path d="M0 0l6 5 6-5" fill="none" stroke="#1e1e1e" stroke-width="1.2"/></svg><span>hello@tidalforge.example</span></div>
  </div>
</div>

<div class="f-col abs" style="left:696px">
  <div class="f-head">MENU</div>
  <div class="f-list menu-list">Home<br>About Us<br>Services<br>Features<br>Blog<br>Contact Us</div>
</div>

<div class="f-head newsletter-head abs">NEWSLETTER</div>
<div class="email-box abs">E-mail id</div>
<div class="btn btn-green newsletter-btn abs">Signup</div>

<div class="f-rule abs"></div>
<div class="follow abs">
  <span class="f-head">FOLLOW US</span>
  <span class="social" style="background:#3b5ba6"></span>
  <span class="social" style="background:#2aa3e0"></span>
  <span class="social" style="background:#1a5fa8"></span>
</div>
<div class="copyright abs">Copyrights @ 2018 All Rights Reserved</div>

</body>
</html>
```